business card design for a plumbing contractor

i need a double business card for a plumbing business, our initial service is residential Sewer Drain Cleaning.

Target Market(s)

other plumbing Business

Industry/Entity Type

Plumbing

Contact Information for Business Card

www.PipeworksTopMark.example- 5307218394-

Font styles to use
Serif

Colors
ec1f27
0455a3

```html
<!DOCTYPE html>
<html lang="en">
<head>
<meta charset="utf-8">
<title>Pipeworks Top Mark – Business Card</title>
<link href="https://fonts.googleapis.com/css2?family=Roboto+Condensed:wght@400;500;700&display=swap" rel="stylesheet">
<style>
  :root {
    --backdrop: #2b2b2b;
    --paper: #efefef;
    --brand-red: #d5352f;
    --brand-taupe: #877f72;
    --logo-ink: #756b5f;
    --white: #ffffff;
  }
  * { box-sizing: border-box; margin: 0; padding: 0; }
  html, body { width: 1200px; height: 960px; overflow: hidden; }
  body {
    background: var(--backdrop);
    font-family: "Roboto Condensed", Arial, sans-serif;
    position: relative;
  }
  .card {
    position: absolute;
    width: 600px;
    height: 343px;
    overflow: hidden;
  }
  .card--front { left: 322px; top: 108px; background: var(--paper); }
  .card--back { left: 320px; top: 493px; background: var(--brand-taupe); }

  .front-brand {
    position: absolute;
    left: 0; top: 0; width: 600px; height: 204px;
    display: flex; align-items: center; justify-content: center;
    gap: 12px;
  }
  .brand-name {
    font-weight: 700;
    font-size: 38px;
    color: var(--logo-ink);
    letter-spacing: 0.5px;
  }
  .brand-square {
    width: 22px; height: 22px;
    background: var(--brand-red);
  }

  .contact-band {
    position: absolute;
    left: 0; top: 204px; width: 600px; height: 139px;
    background: var(--brand-red);
    color: var(--white);
    padding: 18px 0 0 28px;
  }
  .person-name { font-size: 23px; font-weight: 500; line-height: 26px; }
  .person-role { font-size: 15px; font-weight: 400; line-height: 18px; margin-bottom: 14px; }
  .contact-list { list-style: none; font-size: 14px; line-height: 18px; }
  .contact-list li { display: flex; align-items: center; gap: 8px; }
  .contact-list svg { width: 14px; height: 14px; fill: var(--white); flex: none; }

  .back-brand {
    position: absolute;
    left: 0; top: 0; width: 600px; height: 290px;
    display: flex; align-items: center; justify-content: center; gap: 14px;
  }
  .back-brand .brand-name { color: var(--white); font-size: 44px; }
  .back-brand .brand-square { background: var(--white); width: 26px; height: 26px; }
  .service-line {
    position: absolute;
    left: 0; top: 300px; width: 600px;
    text-align: center;
    color: var(--white);
    font-size: 15px;
  }
</style>
</head>
<body>
  <section class="card card--front">
    <div class="front-brand">
      <span class="brand-name">Pipeworks Top Mark</span>
      <span class="brand-square"></span>
    </div>
    <div class="contact-band">
      <p class="person-name">DALE MERCER</p>
      <p class="person-role">CEO/FOUNDER</p>
      <ul class="contact-list">
        <li>
          <svg viewBox="0 0 24 24" aria-hidden="true"><path d="M6.6 10.8a15.1 15.1 0 0 0 6.6 6.6l2.2-2.2c.3-.3.7-.4 1-.2 1.1.4 2.3.6 3.6.6.6 0 1 .4 1 1V20c0 .6-.4 1-1 1A17 17 0 0 1 3 4c0-.6.4-1 1-1h3.5c.6 0 1 .4 1 1 0 1.3.2 2.5.6 3.6.1.3 0 .7-.2 1z"/></svg>
          <span>5307218394</span>
        </li>
        <li>
          <svg viewBox="0 0 24 24" aria-hidden="true"><path d="M2 5h20v14H2z M2 5l10 7 10-7" fill="none" stroke="#fff" stroke-width="0"/><path d="M2 5h20v2l-10 6L2 7z"/><path d="M2 9l10 6 10-6v10H2z"/></svg>
          <span>Dispatcher@PipeworksTopMark.example</span>
        </li>
        <li>
          <svg viewBox="0 0 24 24" aria-hidden="true"><circle cx="12" cy="12" r="10"/><path d="M12 2v20M2 12h20" stroke="#d5352f" stroke-width="1.6"/></svg>
          <span>www.PipeworksTopMark.example</span>
        </li>
      </ul>
    </div>
  </section>

  <section class="card card--back">
    <div class="back-brand">
      <span class="brand-name">Pipeworks Top Mark</span>
      <span class="brand-square"></span>
    </div>
    <p class="service-line">Sewer Drain Cleaning • Maintenance • Trenchless Pipe Installs</p>
  </section>
</body>
</html>
```